QP Fiduciary Website Redesign Contest

We want to refresh our website to be more insitutional, professional for an international audience. We have designed a new logo for this purpose and that has been attached. A full brand brief and positioning statement has also been attached. Please read through all the documents carefully before designing. The old website is found here: https://qp-fiduciary.example/

Target Market(s)

Actuaries and associated businesses internationally

Industry/Entity Type

professional services - actuaries

Number of Pages Required

3 page

Font styles to use
Sans Serif

Colors
0054AA
0677BA
7BADD7
CADEEF
E8F1F8
0094D4
00A9DD
6FCCEA
C7EBF8
E9F6FB
F0912C
F2A743
F7CA91
FBE8D2
FDF5EE
EE7325
F08F49
F5BC92
FAE3D3
FDF4ED
EB3D1F
EC4F4E
F09395
F8D3D4
FCEDEE

Requirements
Must have
• blues and greens to match the logo color, complimentary colors, navigation
Nice to have
• old site: https://qp-fiduciary.example/

```html
<!DOCTYPE html>
<html lang="en">
<head>
<meta charset="utf-8">
<title>QP Fiduciary — Actuarial Software</title>
<link href="https://fonts.googleapis.com/css2?family=Inter:wght@400;500;600;700;800&display=swap" rel="stylesheet">
<style>
:root{
  --primary:#0677BA;
  --accent:#0094D4;
  --deep:#0054AA;
  --sky:#00A9DD;
  --soft:#7BADD7;
  --pale:#CADEEF;
  --ink:#0f1b2a;
  --text:#33404f;
  --muted:#55606e;
  --band:#E8F1F8;
  --white:#ffffff;
  --footer:#0b2240;
}
*{box-sizing:border-box;margin:0;padding:0}
html,body{width:1200px;height:4098px;overflow:hidden}
body{position:relative;font-family:"Inter",Arial,sans-serif;color:var(--text);background:var(--white)}
.abs{position:absolute}
.btn{position:absolute;display:flex;align-items:center;justify-content:space-between;background:var(--primary);color:var(--white);border-radius:24px;font-size:14px;font-weight:500;padding:0 6px 0 24px;text-decoration:none;white-space:nowrap}
.btn .arrow{width:32px;height:32px;border-radius:50%;border:2px solid var(--white);display:flex;align-items:center;justify-content:center}
.section-title{position:absolute;left:0;width:1200px;text-align:center;font-size:35px;font-weight:700;color:var(--ink);letter-spacing:-0.3px;text-transform:uppercase}
.section-title span{color:var(--accent)}
.title-rule{position:absolute;left:578px;width:44px;height:2px;background:var(--accent)}
.section-sub{position:absolute;left:0;width:1200px;text-align:center;font-size:14px;line-height:23px;color:var(--text)}

.site-header{position:absolute;left:0;top:0;width:1200px;height:70px;background:var(--white)}
.brand{position:absolute;display:flex;align-items:center;gap:10px;font-weight:600;letter-spacing:1px;text-transform:uppercase;white-space:nowrap}
.brand .dot{width:14px;height:14px;border-radius:50%;background:var(--accent)}
.nav a{position:absolute;top:27px;font-size:13px;color:var(--ink);text-decoration:none}
.nav a.active{color:var(--accent)}

.hero{position:absolute;left:0;top:70px;width:1200px;height:544px;background:linear-gradient(100deg,#0b2240 0%,#15406b 45%,#3f6f98 75%,#7BADD7 100%)}
.hero h1{position:absolute;left:70px;top:116px;width:470px;font-size:36px;line-height:46px;font-weight:700;color:var(--white);text-transform:uppercase}
.hero p{position:absolute;left:72px;top:312px;width:440px;font-size:13.5px;line-height:23px;color:var(--white)}

.feature-card{position:absolute;top:826px;width:214px;height:256px;background:var(--white);border-radius:6px;box-shadow:0 4px 18px rgba(6,60,110,.09)}
.feature-card svg{position:absolute;left:22px;top:30px}
.feature-card h3{position:absolute;left:22px;top:110px;width:175px;font-size:15px;line-height:20px;font-weight:600;color:var(--ink)}
.feature-card .rule{position:absolute;left:22px;top:152px;width:30px;height:2px;background:var(--accent)}
.feature-card p{position:absolute;left:22px;top:170px;width:160px;font-size:12px;line-height:19px;color:var(--muted)}

.band{position:absolute;left:0;width:1200px;background:var(--band)}
.photo{position:absolute;border-radius:8px}
.solution{position:absolute;left:629px;width:440px;height:120px}
.solution .icon{position:absolute;left:0;top:0;width:71px;height:71px;border-radius:50%;display:flex;align-items:center;justify-content:center}
.solution h3{position:absolute;left:92px;top:0;font-size:15px;font-weight:600;color:var(--ink)}
.solution p{position:absolute;left:92px;top:24px;width:330px;font-size:12px;line-height:19px;color:var(--muted)}
.learn{font-size:12px;color:var(--primary);text-decoration:none;display:flex;align-items:center;gap:10px}
.solution .learn{position:absolute;left:92px;top:96px}

.char-icon{position:absolute;width:76px;height:76px;border-radius:50%;display:flex;align-items:center;justify-content:center}
.char-text{position:absolute;width:260px}
.char-text h3{font-size:15px;font-weight:600;color:var(--ink);margin-bottom:8px}
.char-text p{font-size:12px;line-height:19px;color:var(--muted)}
.char-text.left{text-align:right}

.insight{position:absolute;top:2728px;width:286px;height:366px;background:var(--white);border-radius:6px;overflow:hidden;box-shadow:0 4px 18px rgba(6,60,110,.07)}
.insight .thumb{position:absolute;left:0;top:0;width:286px;height:191px}
.insight h3{position:absolute;left:19px;top:210px;width:255px;font-size:15px;line-height:21px;font-weight:600;color:var(--ink)}
.insight p{position:absolute;left:19px;top:262px;width:245px;font-size:12px;line-height:19px;color:var(--muted)}
.insight .learn{position:absolute;left:19px;top:326px}

.cta{position:absolute;left:142px;top:3345px;width:916px;height:376px;border-radius:16px;background:radial-gradient(circle at 25% 20%,#1d5a92 0%,#0f3460 40%,#081a30 100%);z-index:2}
.cta h2{position:absolute;left:0;top:78px;width:916px;text-align:center;font-size:37px;line-height:48px;font-weight:700;color:var(--white);text-transform:uppercase}
.cta p{position:absolute;left:178px;top:184px;width:560px;text-align:center;font-size:14px;line-height:23px;color:var(--white)}

.site-footer{position:absolute;left:0;top:3616px;width:1200px;height:482px;background:var(--footer);color:var(--white)}
.site-footer h4{position:absolute;top:208px;font-size:16px;font-weight:600;text-transform:uppercase;letter-spacing:.3px}
.quick a{position:absolute;left:576px;font-size:13px;color:var(--white);text-decoration:none}
.contact-row{position:absolute;left:813px;display:flex;gap:14px;font-size:13px;line-height:19px}
.social{position:absolute;top:4058px;width:30px;height:30px;border-radius:50%;background:var(--white);z-index:3}
</style>
</head>
<body>

<header class="site-header">
  <div class="brand" style="left:70px;top:20px;font-size:24px;color:var(--ink)"><span class="dot"></span>QP Fiduciary</div>
  <nav class="nav">
    <a class="active" href="#" style="left:390px">Home</a>
    <a href="#" style="left:461px">Platform</a>
    <a href="#" style="left:544px">Solutions</a>
    <a href="#" style="left:632px">Insights</a>
    <a href="#" style="left:711px">Company</a>
    <a href="#" style="left:802px">Contact</a>
  </nav>
  <a class="btn" href="#" style="left:882px;top:16px;width:246px;height:38px;justify-content:center;padding:0;font-size:13px">Request a Technical Walkthrough</a>
</header>

<section class="hero" role="img" aria-label="Photo of actuaries reviewing financial charts at a meeting table">
  <h1>Actuarial software for structured, auditable financial analysis.</h1>
  <p><strong>QP Fiduciary</strong> develops software that translates established actuarial methodologies into disciplined, decision-ready tools.</p>
  <a class="btn" href="#" style="left:70px;top:374px;width:304px;height:44px">Request A Technical Walkthrough
    <span class="arrow"><svg width="14" height="14" viewBox="0 0 14 14"><path d="M2 7h10M8 3l4 4-4 4" stroke="#fff" stroke-width="1.8" fill="none"/></svg></span></a>
</section>

<h2 class="section-title" style="top:683px">Platform <span>Overview</span></h2>
<div class="title-rule" style="top:735px"></div>
<p class="section-sub" style="top:754px;left:300px;width:600px">Our platform empowers actuaries and risk professionals with tools designed for modern regulatory and business demands.</p>

<div class="feature-card" style="left:142px">
  <svg width="52" height="52" viewBox="0 0 52 52" fill="none" stroke="#0054AA" stroke-width="1.5"><rect x="4" y="10" width="44" height="30" rx="2"/><circle cx="26" cy="8" r="4"/><path d="M14 20h24M14 28h8M30 28h8M26 12v8M18 46h16"/></svg>
  <h3>Structured Workflows</h3><div class="rule"></div>
  <p>that guide users through every step of the analysis process</p>
</div>
<div class="feature-card" style="left:376px">
  <svg width="52" height="52" viewBox="0 0 52 52" fill="none" stroke="#0094D4" stroke-width="1.5"><circle cx="26" cy="26" r="20"/><path d="M14 14l24 24M10 22l20 20M22 10l20 20M8 30l14 14"/></svg>
  <h3>Full Transparency Of Assumptions</h3><div class="rule"></div>
  <p>that guide users through every step of the analysis process</p>
</div>
<div class="feature-card" style="left:610px">
  <svg width="52" height="52" viewBox="0 0 52 52" fill="none" stroke="#0054AA" stroke-width="1.5"><rect x="6" y="6" width="30" height="38" rx="2"/><path d="M12 14h18M12 20h14M12 26h10"/><circle cx="34" cy="32" r="9"/><path d="M40 38l7 7"/></svg>
  <h3>Built-in Auditability</h3><div class="rule"></div>
  <p>that guide users through every step of the analysis process</p>
</div>
<div class="feature-card" style="left:843px">
  <svg width="52" height="52" viewBox="0 0 52 52" fill="none" stroke="#0094D4" stroke-width="1.5"><circle cx="26" cy="26" r="21"/><circle cx="26" cy="26" r="14"/><path d="M18 22l8-5 8 5M19 24v8M26 24v8M33 24v8M17 34h18"/></svg>
  <h3>Robust Governance Features</h3><div class="rule"></div>
  <p>that guide users through every step of the analysis process</p>
</div>

<section class="band" style="top:1167px;height:682px"></section>
<h2 class="section-title" style="top:1235px">Core <span>Solutions</span></h2>
<div class="title-rule" style="top:1287px"></div>
<p class="section-sub" style="top:1306px">Precision-built modules for the most demanding actuarial tasks</p>
<div class="photo" role="img" aria-label="Photo of two hands joining puzzle pieces" style="left:142px;top:1364px;width:423px;height:399px;background:linear-gradient(135deg,#eef4f9 0%,#b9cde0 45%,#2f4a66 80%,#14263b 100%)"></div>

<div class="solution" style="top:1365px">
  <div class="icon" style="background:var(--deep)"><svg width="34" height="34" viewBox="0 0 34 34" fill="none" stroke="#fff" stroke-width="1.5"><circle cx="20" cy="12" r="8"/><path d="M20 4v8h8M3 26l8-4h8l-4 4 12-6M3 30h24"/></svg></div>
  <h3>Reserving &amp; Valuation</h3>
  <p>Perform compliant, repeatable reserving and valuation processes with full traceability and support for multiple actuarial methods and regulatory frameworks.</p>
  <a class="learn" href="#">Learn More <svg width="16" height="10" viewBox="0 0 16 10"><path d="M1 5h13M10 1l4 4-4 4" stroke="#0677BA" stroke-width="1.4" fill="none"/></svg></a>
</div>
<div class="solution" style="top:1513px">
  <div class="icon" style="background:var(--accent)"><svg width="34" height="34" viewBox="0 0 34 34" fill="none" stroke="#fff" stroke-width="1.5"><path d="M6 3h14l6 6v20H6z"/><path d="M10 12h10M10 17h6"/><circle cx="24" cy="25" r="6"/><path d="M24 21v8"/></svg></div>
  <h3>Pricing</h3>
  <p>Build and test pricing models with transparent assumptions, scenario testing, and comparative analytics to support profitable product development.</p>
  <a class="learn" href="#">Learn More <svg width="16" height="10" viewBox="0 0 16 10"><path d="M1 5h13M10 1l4 4-4 4" stroke="#0677BA" stroke-width="1.4" fill="none"/></svg></a>
</div>
<div class="solution" style="top:1661px">
  <div class="icon" style="background:var(--deep)"><svg width="34" height="34" viewBox="0 0 34 34" fill="none" stroke="#fff" stroke-width="1.5"><circle cx="17" cy="13" r="9"/><path d="M17 8v6M17 17v1M3 28l8-4h8l-4 4 12-6"/></svg></div>
  <h3>Enterprise Risk Management</h3>
  <p>Integrate risk metrics, stress testing, and capital modeling in a governed environment to support ORSA, Solvency II, and other ERM requirements.</p>
  <a class="learn" href="#">Learn More <svg width="16" height="10" viewBox="0 0 16 10"><path d="M1 5h13M10 1l4 4-4 4" stroke="#0677BA" stroke-width="1.4" fill="none"/></svg></a>
</div>

<h2 class="section-title" style="top:1913px">Platform <span>Characteristics</span></h2>
<div class="title-rule" style="top:1970px"></div>
<p class="section-sub" style="top:1991px">Engineered for clarity, built to scale across borders</p>

<svg class="abs" style="left:420px;top:2050px" width="360" height="360" viewBox="0 0 360 360" fill="none" stroke="#7BADD7" stroke-width="2"><circle cx="178" cy="178" r="172"/></svg>
<div class="brand" style="left:470px;top:2211px;font-size:26px;color:var(--ink);width:262px;justify-content:center"><span class="dot"></span>QP Fiduciary</div>

<div class="char-icon" style="left:444px;top:2075px;background:var(--deep)"><svg width="38" height="38" viewBox="0 0 38 38" fill="none" stroke="#fff" stroke-width="1.5"><rect x="14" y="3" width="10" height="8"/><rect x="3" y="27" width="8" height="8"/><rect x="15" y="27" width="8" height="8"/><rect x="27" y="27" width="8" height="8"/><path d="M19 11v8M7 27v-8h24v8M19 19v8"/></svg></div>
<div class="char-icon" style="left:680px;top:2075px;background:var(--accent)"><svg width="38" height="38" viewBox="0 0 38 38" fill="none" stroke="#fff" stroke-width="1.5"><circle cx="12" cy="10" r="6"/><circle cx="26" cy="14" r="5"/><path d="M4 32l8-4h8l-4 4 14-7"/></svg></div>
<div class="char-icon" style="left:444px;top:2308px;background:var(--accent)"><svg width="38" height="38" viewBox="0 0 38 38" fill="none" stroke="#fff" stroke-width="1.5"><path d="M6 3h18l6 6v26H6z"/><ellipse cx="18" cy="20" rx="8" ry="5"/><circle cx="18" cy="20" r="2"/></svg></div>
<div class="char-icon" style="left:680px;top:2308px;background:var(--deep)"><svg width="38" height="38" viewBox="0 0 38 38" fill="none" stroke="#fff" stroke-width="1.5"><circle cx="19" cy="17" r="12"/><path d="M14 22v-5M19 22v-9M24 22v-6M6 34l8-5h10l8-4"/></svg></div>

<div class="char-text left" style="left:159px;top:2082px"><h3>Structured Workflows</h3><p>Consistent, repeatable processes from data to disclosure.</p></div>
<div class="char-text" style="left:781px;top:2082px"><h3>Multi-jurisdictional Review Support</h3><p>Localise assumptions, outputs, and reports for any regulator.</p></div>
<div class="char-text left" style="left:159px;top:2315px"><h3>Transparent Assumptions</h3><p>Every assumption exposed, documented, and linked to source.</p></div>
<div class="char-text" style="left:781px;top:2315px"><h3>Comparative Analysis Capability</h3><p>Run scenarios side by side — instantly see impacts.</p></div>

<a class="btn" href="#" style="left:449px;top:2446px;width:302px;height:45px">Request A Technical Walkthrough
  <span class="arrow"><svg width="14" height="14" viewBox="0 0 14 14"><path d="M2 7h10M8 3l4 4-4 4" stroke="#fff" stroke-width="1.8" fill="none"/></svg></span></a>

<section class="band" style="top:2575px;height:684px"></section>
<h2 class="section-title" style="top:2645px">Latest <span>Insights</span></h2>
<div class="title-rule" style="top:2697px"></div>

<article class="insight" style="left:142px">
  <div class="thumb" role="img" aria-label="Photo of a desk with laptop, calculator and financial charts" style="background:linear-gradient(135deg,#CADEEF 0%,#8fb2cf 55%,#4f7698 100%)"></div>
  <h3>Advancing Actuarial Methods in a Changing Regulatory Landscape</h3>
  <p>Exploring how modern tools support evolving best practices in reserving and capital modeling.</p>
  <a class="learn" href="#">Learn More <svg width="16" height="10" viewBox="0 0 16 10"><path d="M1 5h13M10 1l4 4-4 4" stroke="#0677BA" stroke-width="1.4" fill="none"/></svg></a>
</article>
<article class="insight" style="left:457px">
  <div class="thumb" role="img" aria-label="Photo of printed reports and charts beside a laptop" style="background:linear-gradient(135deg,#E9F6FB 0%,#C7EBF8 45%,#6FCCEA 100%)"></div>
  <h3>Governance and Documentation in Actuarial Modeling</h3>
  <p>Why audit trails and assumption transparency are critical for internal and external review.</p>
  <a class="learn" href="#">Learn More <svg width="16" height="10" viewBox="0 0 16 10"><path d="M1 5h13M10 1l4 4-4 4" stroke="#0677BA" stroke-width="1.4" fill="none"/></svg></a>
</article>
<article class="insight" style="left:772px">
  <div class="thumb" role="img" aria-label="Photo of professionals working at laptops in an office" style="background:linear-gradient(135deg,#1a3a5c 0%,#0f2742 55%,#2c5f7a 100%)"></div>
  <h3>Multi-Jurisdictional Actuarial Practice: Challenges &amp; Solutions</h3>
  <p>Strategies for managing compliance across Solvency II, NAIC, and emerging frameworks.</p>
  <a class="learn" href="#">Learn More <svg width="16" height="10" viewBox="0 0 16 10"><path d="M1 5h13M10 1l4 4-4 4" stroke="#0677BA" stroke-width="1.4" fill="none"/></svg></a>
</article>

<a class="btn" href="#" style="left:516px;top:3130px;width:168px;height:45px">Read Insights
  <span class="arrow"><svg width="14" height="14" viewBox="0 0 14 14"><path d="M2 7h10M8 3l4 4-4 4" stroke="#fff" stroke-width="1.8" fill="none"/></svg></span></a>

<footer class="site-footer">
  <div class="brand" style="left:142px;top:198px;font-size:30px;color:var(--white)"><span class="dot"></span>QP Fiduciary</div>
  <p class="abs" style="left:142px;top:272px;width:300px;font-size:12px;line-height:19px">Software that translates actuarial methodologies into disciplined decision-ready analytical tools across diverse regulatory environments.</p>

  <h4 style="left:576px">Quick Links</h4>
  <nav class="quick">
    <a href="#" style="top:244px">Home</a>
    <a href="#" style="top:272px">Platform</a>
    <a href="#" style="top:297px">Solutions</a>
    <a href="#" style="top:322px">Insights</a>
    <a href="#" style="top:348px">Company</a>
    <a href="#" style="top:378px">Contact</a>
  </nav>

  <h4 style="left:813px">Contact Details</h4>
  <div class="contact-row" style="top:244px">
    <svg width="14" height="18" viewBox="0 0 14 18"><path d="M7 1a6 6 0 0 1 6 6c0 4-6 10-6 10S1 11 1 7a6 6 0 0 1 6-6z" fill="#fff"/><circle cx="7" cy="7" r="2.2" fill="#0b2240"/></svg>
    <div><strong style="font-weight:600">QP Fiduciary, Inc.</strong><br>410 Harbor Point Ave, Suite 12<br>Lakeview, FL 33999</div>
  </div>
  <div class="contact-row" style="top:322px;font-weight:600">
    <svg width="16" height="16" viewBox="0 0 16 16"><path d="M3 1l3 3-2 2c1 2 3 4 5 5l2-2 3 3-2 3C7 15 1 9 1 3z" fill="#fff"/></svg>
    +1(555)010-2478
  </div>
  <div class="contact-row" style="top:362px;font-size:12px">
    <svg width="16" height="12" viewBox="0 0 16 12"><rect x="0" y="0" width="16" height="12" rx="1" fill="#fff"/><path d="M1 1l7 6 7-6" stroke="#0b2240" stroke-width="1.4" fill="none"/></svg>
    hello@qp-fiduciary.example
  </div>

  <div class="abs" style="left:142px;top:426px;width:916px;height:1px;background:#2a4466"></div>
  <p class="abs" style="left:142px;top:449px;font-size:12px">© 2026 QP Fiduciary. All rights reserved. &nbsp;&nbsp;&nbsp;&nbsp;&nbsp; Privacy · Terms</p>
</footer>
<span class="social" style="left:949px"></span>
<span class="social" style="left:988px"></span>
<span class="social" style="left:1027px"></span>

<section class="cta" role="img" aria-label="Dark photo of a hand holding a phone with a glowing digital globe">
  <h2>Ready to see the<br>platform in action?</h2>
  <p>Schedule a technical walkthrough and discover how QP Fiduciary can bring structure, transparency, and auditability to your actuarial processes.</p>
  <a class="btn" href="#" style="left:307px;top:247px;width:302px;height:43px">Request A Technical Walkthrough
    <span class="arrow"><svg width="14" height="14" viewBox="0 0 14 14"><path d="M2 7h10M8 3l4 4-4 4" stroke="#fff" stroke-width="1.8" fill="none"/></svg></span></a>
</section>

</body>
</html>
```